Cafe Business needs a business card design

I already have an ai logo I would like to use and color. I need someone to make a business card for me on adobe illustrator with it. Its for a cafe restaurant opening in Japan I would like to be able to change out the names, contact info, ect on my own from adobe illustrator.

Industry/Entity Type

Business

Contact Information for Business Card

Double sided with logo on one side and info on the other. Name, Tel, fax, email and west

```html
<!DOCTYPE html>
<html lang="en">
<head>
<meta charset="utf-8">
<title>Kumo Bean Cafe – Business Card</title>
<link href="https://fonts.googleapis.com/css2?family=Open+Sans:wght@400;600;700&display=swap" rel="stylesheet">
<style>
  :root {
    --backdrop: #e8e3db;
    --card-light: #f7efe2;
    --card-mid: #eadbc4;
    --espresso: #4a2f1f;
    --mocha: #6b4a35;
    --ink: #3a2a20;
    --rule: #cdbba2;
    --white: #ffffff;
  }
  * { margin: 0; padding: 0; box-sizing: border-box; }
  html, body {
    width: 1200px; height: 913px; overflow: hidden;
    background: var(--backdrop);
    font-family: "Open Sans", Arial, sans-serif;
  }
  .stage {
    position: relative; width: 1200px; height: 913px;
    display: flex; align-items: center; justify-content: center; gap: 60px;
  }
  .card {
    position: relative; width: 520px; height: 300px;
    border-radius: 14px; overflow: hidden;
    background: linear-gradient(135deg, var(--card-light) 0%, var(--card-mid) 100%);
    box-shadow: 0 10px 26px rgba(60, 40, 25, 0.22);
  }
  .card-band { position: absolute; inset: 0; width: 100%; height: 100%; }

  /* Front */
  .brand-block {
    position: absolute; top: 24px; right: 34px;
    display: flex; flex-direction: column; align-items: center; gap: 10px;
  }
  .brand-square { width: 124px; height: 96px; background: var(--mocha); }
  .brand-name {
    font-weight: 700; font-size: 17px; letter-spacing: 1.5px;
    color: var(--mocha); white-space: nowrap;
  }
  .holder {
    position: absolute; left: 30px; top: 150px; color: var(--ink);
  }
  .holder-name { font-weight: 600; font-size: 19px; letter-spacing: 0.5px; text-transform: uppercase; }
  .holder-role { font-size: 11px; letter-spacing: 0.8px; text-transform: uppercase; margin-top: 1px; }
  .holder-rule {
    position: absolute; left: 150px; top: 170px; width: 340px; height: 1px;
    background: var(--rule);
  }
  .contact-list {
    position: absolute; left: 40px; top: 196px; list-style: none;
    font-size: 11.5px; line-height: 15px; color: var(--ink);
  }
  .contact-list li { display: flex; align-items: center; gap: 7px; }
  .contact-icon { width: 10px; height: 10px; fill: var(--ink); flex: none; }

  /* Back */
  .back-mark {
    position: absolute; left: 0; right: 0; top: 78px;
    display: flex; align-items: center; justify-content: center; gap: 18px;
  }
  .back-circle { width: 96px; height: 96px; border-radius: 50%; background: var(--mocha); }
  .back-name {
    font-weight: 700; font-size: 30px; letter-spacing: 2px; color: var(--mocha);
  }
</style>
</head>
<body>
<main class="stage">

  <section class="card card-front" aria-label="Business card front">
    <svg class="card-band" viewBox="0 0 520 300" aria-hidden="true">
      <path d="M0 284 H270 C292 284 292 258 316 258 H520" fill="none" stroke="var(--white)" stroke-width="4"/>
      <path d="M0 289 H272 C296 289 296 263 318 263 H520 V300 H0 Z" fill="var(--espresso)"/>
    </svg>

    <div class="brand-block">
      <div class="brand-square"></div>
      <div class="brand-name">KUMO BEAN CAFE</div>
    </div>

    <div class="holder">
      <div class="holder-name">Kenji Arata</div>
      <div class="holder-role">Owner</div>
    </div>
    <div class="holder-rule"></div>

    <ul class="contact-list">
      <li>
        <svg class="contact-icon" viewBox="0 0 10 10"><path d="M2 0.5 L3.6 2.6 L2.7 3.6 C3.3 5 4.9 6.6 6.4 7.3 L7.4 6.4 L9.5 8 L8.4 9.5 C4.5 9.2 0.8 5.5 0.5 1.6 Z"/></svg>
        +81 3-5550-0142
      </li>
      <li>
        <svg class="contact-icon" viewBox="0 0 10 10"><rect x="2.5" y="0.5" width="5" height="3"/><rect x="0.5" y="4" width="9" height="4.5" rx="1"/><rect x="2.5" y="7" width="5" height="2.5"/></svg>
        +81 3-5550-0187
      </li>
      <li>
        <svg class="contact-icon" viewBox="0 0 10 10"><path d="M0.5 2 H9.5 V8.5 H0.5 Z M1.5 3 V7.5 H8.5 V3 L5 5.6 Z M2 3 L5 5 L8 3 Z" fill-rule="evenodd"/></svg>
        kenji@kumobean.jp
      </li>
      <li>
        <svg class="contact-icon" viewBox="0 0 10 10"><circle cx="5" cy="5" r="4.3" fill="none" stroke="var(--ink)" stroke-width="1"/><path d="M0.7 5 H9.3 M5 0.7 C2.8 3 2.8 7 5 9.3 M5 0.7 C7.2 3 7.2 7 5 9.3" fill="none" stroke="var(--ink)" stroke-width="0.8"/></svg>
        www.kumobean.jp
      </li>
    </ul>
  </section>

  <section class="card card-back" aria-label="Business card back">
    <svg class="card-band" viewBox="0 0 520 300" aria-hidden="true">
      <path d="M0 284 H270 C292 284 292 258 316 258 H520" fill="none" stroke="var(--white)" stroke-width="4"/>
      <path d="M0 289 H272 C296 289 296 263 318 263 H520 V300 H0 Z" fill="var(--espresso)"/>
    </svg>
    <div class="back-mark">
      <div class="back-circle"></div>
      <div class="back-name">KUMO BEAN CAFE</div>
    </div>
  </section>

</main>
</body>
</html>
```